U.S. Popcorn company needs business cards

We are a popcorn company that manufactures popcorn and sells it to grocery stores worldwide. Our theme is "Americana" and our logo is U.S. route 66 which is the most famous highway in the U.S.

We would like the design to be simple and to use both sides. On the back side we would like to see just the logo and website. The front would be normal details

Target Market(s)

Wholesalers, grocers and distributors

Industry/Entity Type

Manufacture

Contact Information for Business Card

Business name: Prairie Lantern Popcorn
Phone: +1 555 308 4726
Email: Dale@prairielanternpopcorn.com
website: www.prairielanternpopcorn.com
Tag Line: "Fresh from the heartland"
Name: Dale Whitcombe
Title: Founder/President

Requirements
Must have
• Either this design should be fun or clean and simple. I will let you show me your thougths.
Nice to have
• Anything that ties in the real Hwy Route 66.
• Colors might need to be red, white and blue incorporated.
Should not have
• Not be too busy.

```html
<!DOCTYPE html>
<html lang="en">
<head>
<meta charset="utf-8">
<title>Prairie Lantern Popcorn – Business Cards</title>
<link rel="stylesheet" href="https://fonts.googleapis.com/css2?family=Mulish:ital,wght@0,400;0,600;0,700;0,800;1,400&display=swap">
<style>
  :root {
    --backdrop: #e4e4e4;
    --card: #fafafa;
    --card-edge: #d6d6d6;
    --navy: #1d3473;
    --red: #d2232a;
    --ink: #2a3a78;
  }
  * { box-sizing: border-box; margin: 0; padding: 0; }
  html, body {
    width: 1200px;
    height: 576px;
    overflow: hidden;
    background: var(--backdrop);
    font-family: "Mulish", "Century Gothic", sans-serif;
  }
  .canvas {
    position: relative;
    width: 1200px;
    height: 576px;
  }
  .card {
    position: absolute;
    top: 138px;
    width: 484px;
    height: 294px;
    background: var(--card);
    border: 1px solid var(--card-edge);
    border-radius: 8px;
  }
  .card--back { left: 82px; }
  .card--front { left: 602px; }

  .brand-name {
    color: var(--navy);
    font-weight: 800;
    text-transform: uppercase;
    text-align: center;
    line-height: 1.05;
    letter-spacing: 0.5px;
  }
  .brand-dot {
    display: block;
    width: 14px;
    height: 14px;
    border-radius: 50%;
    background: var(--red);
    margin: 0 auto 8px;
  }

  /* back side */
  .card--back .brand {
    position: absolute;
    left: 0; right: 0;
    top: 92px;
  }
  .card--back .brand-name { font-size: 30px; }
  .back-site {
    position: absolute;
    left: 0; right: 0;
    top: 258px;
    display: flex;
    align-items: center;
    justify-content: center;
    gap: 12px;
    font-size: 11px;
    font-weight: 700;
    color: var(--navy);
  }
  .back-site .rule {
    width: 50px;
    height: 2px;
    background: var(--navy);
    border-radius: 1px;
  }
  .back-site .domain { color: var(--red); }

  /* front side */
  .card--front .brand {
    position: absolute;
    left: 34px;
    top: 86px;
    width: 168px;
  }
  .card--front .brand-name { font-size: 21px; }
  .person {
    position: absolute;
    left: 225px;
    top: 72px;
  }
  .person-name {
    color: var(--red);
    font-size: 16px;
    font-weight: 700;
  }
  .person-title {
    color: var(--ink);
    font-size: 11px;
    font-style: italic;
    margin-top: 2px;
  }
  .contact-list {
    position: absolute;
    left: 225px;
    top: 132px;
    list-style: none;
  }
  .contact-list li {
    display: flex;
    align-items: center;
    gap: 10px;
    height: 17.5px;
    font-size: 13px;
    color: var(--ink);
  }
  .contact-list svg { width: 11px; height: 11px; fill: var(--red); flex: none; }
  .tagline {
    position: absolute;
    left: 0; right: 0;
    top: 245px;
    text-align: center;
    font-size: 15px;
    color: var(--ink);
  }
  .tagline strong { color: var(--red); font-weight: 800; }
</style>
</head>
<body>
<main class="canvas">

  <section class="card card--back" aria-label="Card back">
    <div class="brand">
      <span class="brand-dot"></span>
      <p class="brand-name">Prairie Lantern<br>Popcorn</p>
    </div>
    <p class="back-site">
      <span class="rule"></span>
      <span>www.<span class="domain">prairielanternpopcorn</span>.com</span>
      <span class="rule"></span>
    </p>
  </section>

  <section class="card card--front" aria-label="Card front">
    <div class="brand">
      <span class="brand-dot"></span>
      <p class="brand-name">Prairie Lantern<br>Popcorn</p>
    </div>

    <div class="person">
      <p class="person-name">Dale Whitcombe</p>
      <p class="person-title">Founder/President</p>
    </div>

    <ul class="contact-list">
      <li>
        <svg viewBox="0 0 12 12" aria-hidden="true"><path d="M1 4.2C1 2.6 3.4 1.5 6 1.5S11 2.6 11 4.2V5H8.6V3.9H3.4V5H1Z"/><path d="M2.5 6h7l1 4.5h-9z"/></svg>
        <span>+1 555 308 4726</span>
      </li>
      <li>
        <svg viewBox="0 0 12 12" aria-hidden="true"><path d="M1 2.5h10v1L6 7 1 3.5z"/><path d="M1 5l5 3.5L11 5v4.5H1z"/></svg>
        <span>Dale@prairielanternpopcorn.com</span>
      </li>
      <li>
        <svg viewBox="0 0 12 12" aria-hidden="true"><path fill-rule="evenodd" d="M6 1a5 5 0 1 1 0 10A5 5 0 0 1 6 1Zm-.6 1.2A3.9 3.9 0 0 0 2.1 5.4h1.8c.1-1.2.6-2.3 1.5-3.2Zm1.2 0c.9.9 1.4 2 1.5 3.2h1.8a3.9 3.9 0 0 0-3.3-3.2ZM5 5.4h2C6.9 4.4 6.6 3.5 6 2.8 5.4 3.5 5.1 4.4 5 5.4Zm-2.9 1.2a3.9 3.9 0 0 0 3.3 3.2c-.9-.9-1.4-2-1.5-3.2Zm2.9 0c.1 1 .4 1.9 1 2.6.6-.7.9-1.6 1-2.6Zm3.1 0c-.1 1.2-.6 2.3-1.5 3.2a3.9 3.9 0 0 0 3.3-3.2Z"/></svg>
        <span>www.prairielanternpopcorn.com</span>
      </li>
    </ul>

    <p class="tagline">"<strong>Fresh</strong> from the heartland"</p>
  </section>

</main>
</body>
</html>
```